New Webpage for High Class Expert Witness Services Company

We are looking for a minimalist design for a webpage that just has our logo and an entry form offer to connect with one of our Liaisons.
The entry form should just ask for Name, Email, Contact Info and Description of Project.

Company Name is: The Marlowe Crest Advisory Services

Number of Pages Required

1 page

```html
<!DOCTYPE html>
<html lang="en">
<head>
<meta charset="UTF-8">
<title>The Marlowe Crest Advisory Services — Get in Touch</title>
<link href="https://fonts.googleapis.com/css2?family=Cinzel:wght@400;500&family=Poppins:ital,wght@0,300;0,400;0,500;1,400&display=swap" rel="stylesheet">
<style>
  :root{
    --ink:#1a1a1a;
    --ink-soft:#3a3a3a;
    --muted:#6b6b6b;
    --line:#b9b9bd;
    --hero-a:#e2e2e6;
    --hero-b:#b4b4ba;
    --panel:#1d1d1e;
    --panel-hi:#262627;
    --white:#ffffff;
    --footer:#111111;
  }
  *{box-sizing:border-box;margin:0;padding:0}
  html,body{width:1200px;height:1012px;overflow:hidden;background:var(--white)}
  body{position:relative;font-family:"Poppins",sans-serif;color:var(--ink)}
  .hero-bg{position:absolute;left:0;top:0;width:1200px;height:424px;
    background:linear-gradient(135deg,var(--hero-a) 0%,#cbcbd0 50%,var(--hero-b) 100%)}
  .brand{position:absolute;left:145px;top:26px;display:flex;align-items:center;gap:10px}
  .brand-mark{width:14px;height:14px;background:var(--ink-soft)}
  .brand-name{font-family:"Cinzel",serif;font-weight:500;font-size:19px;letter-spacing:.5px;color:var(--ink-soft);line-height:1.1}
  .contact-btn{position:absolute;left:925px;top:22px;width:134px;height:42px;border:1.3px solid var(--ink);border-radius:6px;
    display:flex;align-items:center;justify-content:center;gap:8px;font-size:13px;font-weight:500;color:var(--ink)}
  .header-rule{position:absolute;left:141px;top:85px;width:918px;height:1px;background:#9d9da2}
  .hero-title{position:absolute;left:0;width:1200px;top:148px;text-align:center;font-family:"Cinzel",serif;font-size:38px;font-weight:400;color:var(--ink)}
  .hero-text{position:absolute;left:230px;width:740px;top:202px;text-align:center;font-size:13.3px;line-height:22.6px;color:var(--ink-soft)}
  .card{position:absolute;left:141px;top:312px;width:918px;height:487px;background:var(--white);border-radius:10px;
    box-shadow:0 14px 40px rgba(0,0,0,.10)}
  .info-panel{position:absolute;left:155px;top:325px;width:374px;height:461px;border-radius:9px;overflow:hidden;
    background:linear-gradient(160deg,#232324,#171718)}
  .info-panel .deco{position:absolute;left:0;top:0}
  .info-title{position:absolute;left:29px;top:34px;font-family:"Cinzel",serif;font-size:32px;color:var(--white)}
  .info-text{position:absolute;left:29px;top:80px;width:320px;font-size:12.6px;line-height:19px;color:#e6e6e6}
  .info-item{position:absolute;left:29px;display:flex;gap:18px}
  .info-item svg{margin-top:8px;flex:none}
  .info-label{font-size:12.3px;color:#e0e0e0;line-height:18px}
  .info-value{font-size:15.5px;font-weight:500;color:var(--white);margin-top:6px}
  .field{position:absolute;width:219px;border-bottom:1px solid var(--line);padding-bottom:13px}
  .field-label{font-size:12.6px;color:var(--muted)}
  .field-value{font-size:14.5px;color:var(--ink);margin-top:5px}
  .field.wide{width:462px;height:83px}
  .field.wide .field-label{color:var(--ink)}
  .placeholder{font-size:11.2px;color:#8a8a8a;margin-top:8px}
  .submit-btn{position:absolute;left:778px;top:693px;width:247px;height:45px;background:#111;border-radius:6px;
    display:flex;align-items:center;justify-content:center;gap:10px;color:var(--white);font-size:12.5px;font-weight:500;
    box-shadow:0 6px 14px rgba(0,0,0,.18)}
  .notice{position:absolute;left:0;width:1200px;top:834px;display:flex;justify-content:center;align-items:center;gap:12px;
    font-size:13px;font-style:italic;color:#666}
  .footer{position:absolute;left:0;top:941px;width:1200px;height:71px;background:var(--footer);
    display:flex;align-items:center;justify-content:center;color:#eee;font-size:13px}
</style>
</head>
<body>
  <div class="hero-bg" role="img" aria-label="Soft grey geometric cube texture background"></div>

  <header>
    <div class="brand"><span class="brand-mark"></span><span class="brand-name">The Marlowe Crest<br>Advisory Services</span></div>
    <div class="contact-btn">Contact Us
      <svg width="18" height="10" viewBox="0 0 18 10"><path d="M1 5h15M12 1l4 4-4 4" fill="none" stroke="#1a1a1a" stroke-width="1.8" stroke-linecap="round" stroke-linejoin="round"/></svg>
    </div>
    <div class="header-rule"></div>
  </header>

  <h1 class="hero-title">GET IN TOUCH</h1>
  <p class="hero-text">Lorem ipsum dolor sit amet, consectetuer adipiscing elit. Aenean commodo ligula eget dolor. Aenean massa. Cum sociis natoque penatibus et magnis dis parturient montes, nascetur ridiculus mus. Donec quam felis,</p>

  <section class="card"></section>

  <aside class="info-panel">
    <svg class="deco" width="374" height="461" viewBox="0 0 374 461">
      <circle cx="330" cy="415" r="185" fill="#202021"/>
      <circle cx="330" cy="415" r="110" fill="var(--panel-hi)"/>
    </svg>
    <h2 class="info-title">GET IN TOUCH</h2>
    <p class="info-text">Lorem ipsum dolor amet, consectetuer Aenean adipiscing elit. Aenean ligula eget dolor.</p>

    <div class="info-item" style="top:150px">
      <svg width="30" height="30" viewBox="0 0 30 30" fill="none" stroke="#fff" stroke-width="1.5" stroke-linecap="round" stroke-linejoin="round">
        <path d="M7 3l4 5-2.5 3c1.5 3.5 4.5 6.5 8 8l3-2.5 5 4-2 4c-8 1-19-10-18-19z"/>
        <path d="M17 6a7 7 0 0 1 7 7M18 2a11 11 0 0 1 10 10"/>
      </svg>
      <div><div class="info-label">Phone Number:</div><div class="info-value">+61 (123) 555 0190</div></div>
    </div>
    <div class="info-item" style="top:230px">
      <svg width="30" height="30" viewBox="0 0 30 30" fill="none" stroke="#fff" stroke-width="1.6" stroke-linejoin="round">
        <rect x="1.5" y="5" width="27" height="20" rx="1.5"/><path d="M2 6l13 11L28 6M2 24l10-9M28 24l-10-9"/>
      </svg>
      <div><div class="info-label">Email Address:</div><div class="info-value">info@marlowecrest.co</div></div>
    </div>
    <div class="info-item" style="top:309px">
      <svg width="30" height="30" viewBox="0 0 30 30" fill="none" stroke="#fff" stroke-width="1.5" stroke-linejoin="round">
        <path d="M15 22s-7-6.5-7-12a7 7 0 0 1 14 0c0 5.5-7 12-7 12z"/><circle cx="15" cy="10" r="2.6"/>
        <path d="M10 20c-4 .8-6 2-6 3.3 0 2 5 3.2 11 3.2s11-1.2 11-3.2c0-1.3-2-2.5-6-3.3"/>
      </svg>
      <div><div class="info-label">Location:</div><div class="info-value">New York, SISA</div></div>
    </div>
  </aside>

  <form>
    <div class="field" style="left:563px;top:370px"><div class="field-label">First Name</div><div class="field-value">Avery</div></div>
    <div class="field" style="left:806px;top:370px"><div class="field-label">Last Name</div><div class="field-value">Dunmore</div></div>
    <div class="field" style="left:563px;top:469px"><div class="field-label">Your Email</div><div class="field-value">averydunmore@mail.com</div></div>
    <div class="field" style="left:806px;top:469px"><div class="field-label">Your Contact</div><div class="field-value">125 555 0147</div></div>
    <div class="field wide" style="left:563px;top:568px"><div class="field-label">Description of Project</div><div class="placeholder">Write here your message...</div></div>
    <div class="submit-btn">CONNECT WITH A LIAISON
      <svg width="22" height="12" viewBox="0 0 22 12"><path d="M1 6h19M15 1l5 5-5 5" fill="none" stroke="#fff" stroke-width="2" stroke-linecap="round" stroke-linejoin="round"/></svg>
    </div>
  </form>

  <p class="notice">
    <svg width="18" height="22" viewBox="0 0 18 22" fill="none" stroke="#777" stroke-width="1.4"><rect x="1.5" y="9" width="15" height="11.5" rx="2"/><path d="M4.5 9V6a4.5 4.5 0 0 1 9 0v3"/><circle cx="9" cy="14" r="1.3"/><path d="M9 15.3v2"/></svg>
    Strictly confidential, deliver directly to the assigned case officer.
  </p>

  <footer class="footer">© 2026 the marlowe crest advisory services all right</footer>
</body>
</html>
```